Keystone Trench Co Business Card*

Looking for a professional, clean and crisp business card

I am in the underground utilities industry and am just looking for a really impressive business card. I would like our card to be white with our symbol crisp and clear with it protruding. I also have a business partner that will require his name and info on the card once the design is set. I would like to have our website info on the card which is;
http://keystonetrenchco.example/

Contact Information for Business Card

Website, contact name, number and email

```html
<!DOCTYPE html>
<html lang="en">
<head>
<meta charset="utf-8">
<title>Keystone Trench Co Business Card</title>
<link rel="stylesheet" href="https://fonts.googleapis.com/css2?family=Open+Sans:wght@400;600;700&display=swap">
<style>
  :root {
    --stage: #262626;
    --card-dark: #1c1c1c;
    --card-light: #ffffff;
    --brand-blue: #3f63ad;
    --ink: #1a1a1a;
    --icon-red: #e0262b;
    --rule: #222222;
    --faint: #ececec;
  }
  * { box-sizing: border-box; margin: 0; padding: 0; }
  html, body { width: 1200px; height: 895px; overflow: hidden; }
  body {
    background: var(--stage);
    font-family: "Open Sans", Arial, sans-serif;
    position: relative;
  }
  .card {
    position: absolute;
    width: 560px;
    height: 320px;
    overflow: hidden;
    box-shadow: 0 18px 40px rgba(0,0,0,.55);
  }
  .card__band {
    position: absolute;
    left: 0; right: 0; bottom: 0;
    height: 7px;
    background: var(--brand-blue);
  }
  /* Back */
  .card--back { left: 60px; top: 70px; background: var(--card-dark); }
  .card--back .brand-mark {
    position: absolute;
    left: 0; right: 0; top: 130px;
    display: flex; align-items: center; justify-content: center; gap: 12px;
    color: var(--card-light);
  }
  /* Front */
  .card--front { left: 580px; top: 505px; background: var(--card-light); }
  .brand-mark {
    font-weight: 700;
    font-size: 24px;
    letter-spacing: .5px;
  }
  .brand-mark__dot {
    width: 18px; height: 18px; border-radius: 50%;
    background: var(--brand-blue);
  }
  .card--front .brand-mark {
    position: absolute;
    right: 34px; top: 46px;
    display: flex; align-items: center; gap: 10px;
    color: var(--ink);
    font-size: 20px;
  }
  .faint-mark {
    position: absolute;
    left: 150px; bottom: 26px;
    font-weight: 700;
    font-size: 40px;
    color: var(--faint);
    white-space: nowrap;
  }
  .divider {
    position: absolute;
    left: 200px; right: 48px; top: 140px;
    height: 1.5px;
    background: var(--rule);
  }
  .contact {
    position: absolute;
    right: 22px; top: 156px;
    list-style: none;
    text-align: right;
    font-size: 15px;
    line-height: 22px;
    color: var(--ink);
  }
  .contact li { display: flex; justify-content: flex-end; align-items: center; gap: 9px; }
  .contact svg { width: 14px; height: 14px; flex: none; }
  .person {
    position: absolute;
    left: 38px; top: 214px;
  }
  .person__name {
    font-weight: 700;
    font-size: 24px;
    color: var(--brand-blue);
    letter-spacing: 1px;
    text-transform: uppercase;
  }
  .person__role, .person__company {
    font-size: 15px;
    color: var(--ink);
    letter-spacing: .5px;
  }
  .person__role { text-align: right; }
</style>
</head>
<body>

<section class="card card--back" aria-label="Card back">
  <div class="brand-mark"><span class="brand-mark__dot"></span>Keystone Trench Co</div>
  <div class="card__band"></div>
</section>

<section class="card card--front" aria-label="Card front">
  <div class="faint-mark" aria-hidden="true">Keystone Trench Co</div>
  <div class="brand-mark"><span class="brand-mark__dot"></span>Keystone Trench Co</div>
  <div class="divider"></div>
  <ul class="contact">
    <li>604-555-0182
      <svg viewBox="0 0 14 14"><path d="M3 2c-1 1-1 3 1 6s4 4 5.5 4.5l1.5-1.5-2-2-1.2 1C6.5 9 5 7.5 4 5.7l1-1.2-2-2.5z" fill="var(--icon-red)"/></svg>
    </li>
    <li>dale@keystonetrenchco.example
      <svg viewBox="0 0 14 14"><rect x="1" y="3" width="12" height="8" fill="none" stroke="var(--icon-red)" stroke-width="1.4"/><path d="M1 3l6 5 6-5" fill="none" stroke="var(--icon-red)" stroke-width="1.4"/></svg>
    </li>
    <li>www.keystonetrenchco.example
      <svg viewBox="0 0 14 14"><circle cx="7" cy="7" r="6" fill="var(--icon-red)"/><path d="M1 7h12M7 1v12M3 3.5h8M3 10.5h8" stroke="#fff" stroke-width=".9" fill="none"/></svg>
    </li>
  </ul>
  <div class="person">
    <div class="person__name">Dale Whitcombe</div>
    <div class="person__role">Owner</div>
    <div class="person__company">Keystone Trench Co Inc.</div>
  </div>
  <div class="card__band"></div>
</section>

</body>
</html>
```